New business card for a regional office of a US M&A company

We need business card for a finance company, office based in Hong Kong , our Head office is in US, our business is to Merge and acquires companies , the new office will be a regional office for the Asia Pacific region. We want to use the head office logo as attached ( but don't have to be exactly the same, can be a variation to it) as a base and then add Asia Pacific alongside the logo.
We would prefer to have be bilingual Eng + Chinese, although we don't really have Chinese company name .

Industry/Entity Type

Business

Contact Information for Business Card

Clara Jo Tsang
 

VP,
APAC M&A Operations
ORIN VANTAGE Asia Pacific Limited
 
Unit 1407, K18
18 Tai Lok Shan Road, 
Hong Kong 
 
M: +852 6038 1742
T : +852 2836 4100
F : +852 2836 4177
VOIP: 4158
 
cjtsang@orinvantage.com

Font styles to use
Serif
Sans Serif

Colors

Designer to choose colors to be used in the design.

Requirements
Must have
• APAC Office

```html
<!DOCTYPE html>
<html lang="en">
<head>
<meta charset="utf-8">
<title>Orin Vantage – APAC Business Card</title>
<link rel="stylesheet" href="https://fonts.googleapis.com/css2?family=Open+Sans:wght@400;600;800&display=swap">
<style>
  :root {
    --navy: #0f2a47;
    --navy-soft: #1b3b5e;
    --cyan: #22b5cc;
    --ink: #4a4f55;
    --paper: #ffffff;
    --backdrop: #e4e6e8;
  }
  * { margin: 0; padding: 0; box-sizing: border-box; }
  html, body { width: 1200px; height: 900px; overflow: hidden; }
  body {
    background: var(--backdrop);
    font-family: "Open Sans", Arial, sans-serif;
    position: relative;
  }
  .card {
    position: absolute;
    width: 600px;
    height: 343px;
    overflow: hidden;
    box-shadow: 0 6px 18px rgba(0,0,0,0.18);
  }

  /* Back of card */
  .card-back { left: 440px; top: 60px; background: var(--navy); }
  .card-back .world-area {
    position: absolute; left: 70px; top: 40px; width: 470px; height: 250px;
    border-radius: 40% 45% 40% 50%;
    background: radial-gradient(ellipse at center, var(--navy-soft) 0%, rgba(27,59,94,0.35) 60%, rgba(15,42,71,0) 100%);
  }
  .card-back .brand-lockup {
    position: absolute; left: 0; right: 0; top: 118px;
    display: flex; flex-direction: column; align-items: center; gap: 16px;
  }
  .card-back .brand-square { width: 44px; height: 44px; background: var(--paper); }
  .card-back .brand-name {
    color: var(--paper); font-weight: 800; font-size: 40px; letter-spacing: 2px;
  }

  /* Front of card */
  .card-front { left: 160px; top: 470px; background: var(--paper); }
  .card-front .brand-name {
    position: absolute; left: 34px; top: 20px;
    color: var(--cyan); font-weight: 800; font-size: 38px; letter-spacing: 1.5px;
  }
  .card-front .person-name {
    position: absolute; left: 36px; top: 90px;
    color: var(--navy); font-weight: 600; font-size: 20px; letter-spacing: 0.5px;
  }
  .card-front .person-role {
    position: absolute; left: 36px; top: 117px;
    color: var(--ink); font-weight: 600; font-size: 13px;
  }
  .contact-list {
    position: absolute; left: 36px; top: 150px; list-style: none;
    color: var(--ink); font-size: 13.5px; line-height: 18px; letter-spacing: 0.4px;
  }
  .contact-list li { display: flex; align-items: center; gap: 10px; }
  .contact-list svg { width: 11px; height: 11px; fill: var(--cyan); flex: none; }
  .office-address {
    position: absolute; left: 36px; top: 236px;
    color: var(--ink); font-size: 14.5px; line-height: 20px;
  }
  .brand-mark {
    position: absolute; left: 388px; top: 76px; width: 150px; height: 150px;
    border-radius: 50%; background: var(--navy);
  }
  .stripe-left {
    position: absolute; left: 0; top: 292px; width: 362px; height: 7px; background: var(--cyan);
  }
  .stripe-right {
    position: absolute; right: 0; top: 292px; width: 84px; height: 7px; background: var(--cyan);
  }
  .voip {
    position: absolute; left: 392px; top: 284px;
    color: var(--navy); font-weight: 600; font-size: 13px; letter-spacing: 1.5px;
  }
  .footer-band {
    position: absolute; left: 0; right: 0; bottom: 0; height: 36px; background: var(--navy);
  }
</style>
</head>
<body>

  <section class="card card-back" aria-label="Card back">
    <div class="world-area" role="img" aria-label="Faint dotted world map"></div>
    <div class="brand-lockup">
      <div class="brand-square"></div>
      <div class="brand-name">ORIN VANTAGE</div>
    </div>
  </section>

  <section class="card card-front" aria-label="Card front">
    <div class="brand-name">ORIN VANTAGE</div>
    <div class="person-name">CLARA JO TSANG</div>
    <div class="person-role">VP, APAC M&amp;A Operations</div>

    <ul class="contact-list">
      <li><svg viewBox="0 0 12 12"><rect x="3" y="0.5" width="6" height="11" rx="1" fill="none" stroke="#22b5cc" stroke-width="1.2"/></svg>+852 6038 1742</li>
      <li><svg viewBox="0 0 12 12"><path d="M2 1l2.5-.5 1.2 2.8-1.4 1a6 6 0 0 0 3.4 3.4l1-1.4 2.8 1.2L11 10c-5 .5-9.5-4-9-9z"/></svg>+852 2836 4100</li>
      <li><svg viewBox="0 0 12 12"><rect x="3" y="1" width="6" height="3"/><rect x="1" y="4.5" width="10" height="5" rx="1"/><rect x="3" y="8" width="6" height="3"/></svg>+852 2836 4177</li>
      <li><svg viewBox="0 0 12 12"><rect x="0.5" y="2" width="11" height="8" rx="1"/><path d="M1 2.5l5 4 5-4" fill="none" stroke="#fff" stroke-width="1"/></svg>cjtsang@orinvantage.com</li>
    </ul>

    <div class="office-address">Unit 1407, K18 18 Tai Lok<br>Shan Road, Hong Kong</div>

    <div class="brand-mark"></div>

    <div class="stripe-left"></div>
    <div class="voip">VOIP: 4158</div>
    <div class="stripe-right"></div>
    <div class="footer-band"></div>
  </section>

</body>
</html>
```